Letter design, envelope design, and more

Hello, we the Tavrin Gmbh are looking for our shop. Letter C5. Design does not have to be like a business card, so it can have straight lines. Only the color is important. The logo is the text under TaVRin omit.It should not be playful but Profesionel

Font styles to use
Sans Serif

Colors
0555a3
3176b5
85abd2
85cae6
34a7d8
0792cd
cee9f5
cfdfed
000000

Requirements
Must have
• Color like business card, Please, with the text under TaVRin, Correct address Lindmattstr. 4 Zip code 9517 Tannwil, as well as Couvert Without addressing only design and logo with TaVrn
Nice to have
• more writing articles
Should not have
• Not too colored, Text under TaVRin, bright colors

```html
<!DOCTYPE html>
<html lang="en">
<head>
<meta charset="utf-8">
<title>Tavrin Gmbh – Stationery</title>
<link href="https://fonts.googleapis.com/css2?family=Lato:wght@400;700&family=Yellowtail&display=swap" rel="stylesheet">
<style>
  :root{
    --stage:#dfe1e3;
    --paper:#ffffff;
    --navy:#2b2d6e;
    --slate:#7d93aa;
    --ink:#4a4a4f;
    --rule:#c9ccd1;
  }
  *{box-sizing:border-box;margin:0;padding:0}
  html,body{width:1200px;height:657px;overflow:hidden;background:var(--stage)}
  body{position:relative;font-family:'Lato',sans-serif;color:var(--ink)}

  .brand{position:absolute;display:flex;align-items:center;gap:8px}
  .brand__square{width:22px;height:22px;background:var(--navy)}
  .brand__name{font-family:'Lato',sans-serif;font-weight:700;color:var(--navy);letter-spacing:1px;white-space:nowrap}

  /* Letterhead */
  .letter{position:absolute;left:51px;top:62px;width:380px;height:534px;
    background:linear-gradient(180deg,#ffffff 0%,#f6f6f7 45%,#ececee 100%);
    border:1px solid var(--rule);overflow:hidden}
  .letter .brand{left:22px;top:24px}
  .letter .brand__name{font-size:22px}
  .contact{position:absolute;left:273px;top:12px;border-left:1px solid var(--slate);
    padding-left:6px;font-size:7.4px;line-height:9px;color:#333;white-space:nowrap}
  .contact__item{display:flex;gap:4px;margin-bottom:5px}
  .contact__icon{width:7px;height:7px;flex:none;margin-top:1px}
  .greeting{position:absolute;left:22px;top:94px;font-size:10px;font-weight:700;color:var(--navy)}
  .body-copy{position:absolute;left:22px;width:341px;font-size:7.1px;line-height:11.6px;color:#555;text-align:justify}
  .closing{position:absolute;left:22px;top:414px;font-size:12px;color:#444}
  .signature{position:absolute;left:22px;top:432px;font-family:'Yellowtail',cursive;font-size:21px;color:var(--navy)}
  .footer-band{position:absolute;left:0;bottom:0}
  .footer-band__url{position:absolute;right:18px;bottom:2px;color:#fff;font-size:9.5px;letter-spacing:2.4px}

  /* Envelopes */
  .envelope{position:absolute;width:563px;height:252px;background:var(--paper);border:1px solid var(--rule);overflow:hidden}
  .envelope--back{left:585px;top:79px}
  .envelope--open{left:545px;top:187px}
  .envelope--front{left:450px;top:299px;height:253px}
  .envelope__flap{position:absolute;left:0;top:0}
  .envelope--back .brand{left:50%;top:30px;transform:translateX(-50%)}
  .envelope--back .brand__name{color:#fff;font-size:24px}
  .envelope--open .brand{left:50%;top:40px;transform:translateX(-50%)}
  .envelope--open .brand__name{font-size:24px}
  .envelope--front .brand{left:23px;top:16px}
  .envelope--front .brand__name{font-size:26px}
  .envelope--front .brand__square{width:26px;height:26px}
  .sender{position:absolute;left:23px;top:66px;display:flex;align-items:center;gap:4px;font-size:10px;color:#222;white-space:nowrap}
  .sender svg{width:9px;height:9px}
</style>
</head>
<body>

<section class="letter">
  <div class="brand"><span class="brand__square"></span><span class="brand__name">TAVRIN</span></div>

  <div class="contact">
    <div class="contact__item">
      <svg class="contact__icon" viewBox="0 0 10 10"><circle cx="5" cy="5" r="4.2" fill="none" stroke="var(--navy)" stroke-width="1"/><circle cx="5" cy="4.3" r="1.4" fill="var(--navy)"/></svg>
      <div>Lindmattstr. 4<br>Zip code 9517 Tannwil</div>
    </div>
    <div class="contact__item">
      <svg class="contact__icon" viewBox="0 0 10 10"><circle cx="5" cy="5" r="4.2" fill="none" stroke="var(--navy)" stroke-width="1"/><path d="M3.5 3 L4.5 3 L5 4.3 L4.3 4.8 Q4.8 5.9 5.6 6.3 L6.1 5.6 L7.2 6.1 L7 7.2 Q4 7.2 3.2 3.9Z" fill="var(--navy)"/></svg>
      <div>+41 71 555 24 80</div>
    </div>
    <div class="contact__item">
      <svg class="contact__icon" viewBox="0 0 10 10"><rect x="1" y="2.5" width="8" height="5.5" fill="var(--navy)"/><path d="M1 2.5 L5 5.6 L9 2.5" fill="none" stroke="#fff" stroke-width=".8"/></svg>
      <div>info@tavrin.ch</div>
    </div>
  </div>

  <p class="greeting">Dear Mr. Lorem,</p>

  <p class="body-copy" style="top:112px">Lorem ipsum dolor sit amet, consectetuer adipiscing elit, sed diam nonummy nibh euismod tincidunt ut laoreet dolore magna aliquam erat volutpat. Ut wisi enim ad minim veniam, quis nostrud exerci tation ullamcorper suscipit lobortis nisl ut aliquip ex ea commodo consequat. Duis autem vel eum iriure dolor in hendiusto odio dignissim qui blandit praesent luptatum zzril delenit facilisi.</p>
  <p class="body-copy" style="top:166px">Lorem ipsum dolor sit amet, consectetuer adipiscing elit, sed diam nonummy nibh euismod tincidunt ut laoreet dolore magna aliquam erat volutpat. Ut wisi enim ad minim veniam, quis nostrud exerci tation ullamcorper suscipit lobortis nisl ut aliquip ex ea commodo consequat.</p>
  <p class="body-copy" style="top:210px">Lorem ipsum dolor sit amet, consectetuer adipiscing elit, sed diam nonummy nibh euismod tincidunt ut laoreet dolore magna aliquam erat volutpat. Ut wisi enim ad minim veniam, quis nostrud exerci tation ullamcorper suscipit lobortis nisl ut aliquip ex ea commodo consequat. Duis autem vel eum iriure dolor in hendiusto odio dignissim qui blandit praesent luptatum zzril delenit facilisi.</p>
  <p class="body-copy" style="top:266px">Lorem ipsum dolor sit amet, consectetuer adipiscing elit, sed diam nonummy nibh euismod tincidunt ut laoreet dolore magna aliquam erat volutpat. Ut wisi enim ad minim veniam, quis nostrud exerci tation ullamcorper suscipit lobortis nisl ut aliquip ex ea commodo consequat.</p>
  <p class="body-copy" style="top:310px">Lorem ipsum dolor sit amet, consectetuer adipiscing elit, sed diam nonummy nibh euismod tincidunt ut laoreet dolore magna aliquam erat volutpat. Ut wisi enim ad minim veniam, quis nostrud exerci tation ullamcorper suscipit lobortis nisl ut aliquip ex ea commodo consequat. Duis autem vel eum iriure dolor in hendiusto odio dignissim qui blandit praesent luptatum zzril delenit facilisi.</p>
  <p class="body-copy" style="top:364px">Lorem ipsum dolor sit amet, consectetuer adipiscing elit, sed diam nonummy nibh euismod tincidunt ut laoreet dolore magna aliquam erat volutpat. Ut wisi enim ad minim veniam, quis nostrud exerci tation ullamcorper suscipit lobortis nisl ut aliquip ex ea commodo consequat.</p>

  <p class="closing">Sincerely Your,</p>
  <p class="signature">Your Name</p>

  <div class="footer-band">
    <svg width="380" height="17" viewBox="0 0 380 17">
      <polygon points="0,9 245,9 240,17 0,17" fill="var(--slate)"/>
      <polygon points="252,0 380,0 380,17 238,17" fill="var(--navy)"/>
    </svg>
    <span class="footer-band__url">www.tavrin.ch</span>
  </div>
</section>

<section class="envelope envelope--back">
  <svg class="envelope__flap" width="563" height="100" viewBox="0 0 563 100">
    <path d="M0 0 H563 C557 30 546 45 520 52 L292 98 Q282 100 272 98 L42 52 C17 45 6 30 0 0Z" fill="var(--slate)"/>
  </svg>
  <div class="brand"><span class="brand__name">TAVRIN</span></div>
</section>

<section class="envelope envelope--open">
  <svg class="envelope__flap" width="563" height="100" viewBox="0 0 563 100">
    <path d="M0 0 C6 30 17 45 42 52 L272 98 Q282 100 292 98 L520 52 C546 45 557 30 563 0" fill="none" stroke="#b7bcc3" stroke-width="1"/>
  </svg>
  <div class="brand"><span class="brand__square"></span><span class="brand__name">TAVRIN</span></div>
</section>

<section class="envelope envelope--front">
  <div class="brand"><span class="brand__square"></span><span class="brand__name">TAVRIN</span></div>
  <div class="sender">
    <svg viewBox="0 0 10 10"><circle cx="5" cy="5" r="4.2" fill="none" stroke="var(--navy)" stroke-width="1"/><circle cx="5" cy="4.3" r="1.4" fill="var(--navy)"/></svg>
    <span>Lindmattstr. 4, Zip code 9517 Tannwil</span>
  </div>
  <div class="footer-band">
    <svg width="563" height="17" viewBox="0 0 563 17">
      <polygon points="0,9 418,9 412,17 0,17" fill="var(--slate)"/>
      <polygon points="426,0 563,0 563,17 410,17" fill="var(--navy)"/>
    </svg>
    <span class="footer-band__url">www.tavrin.ch</span>
  </div>
</section>

</body>
</html>
```